Government contracting small business needs a web design

Tarvex Summit Inc is a veteran owned small business that delivers a full range of professional services as well as training in information technology, security and defense intelligence solutions.
We need a professional/corporate looking website where potential clients can view what services are offered.
This being a new company, there is not much that can added more than a narrative statement, stock photos and a place where potential customers and employees can make contact.
Open to ideas.
Target Market(s)
US Government
Industry/Entity Type
Small Business
Look and feel
Each slider illustrates characteristics of the customer's brand and the style your logo design should communicate.

```html
<!DOCTYPE html>
<html lang="en">
<head>
<meta charset="utf-8">
<title>Tarvex Summit Inc</title>
<link href="https://fonts.googleapis.com/css2?family=Oswald:wght@400;500;600&family=Carlito:wght@400;700&family=Open+Sans:wght@300;400&display=swap" rel="stylesheet">
<style>
  :root {
    --ink: #232323;
    --page: #ffffff;
    --gold: #e8b44a;
    --gold-deep: #c99221;
    --text: #1f1f1f;
    --muted: #5a5a5a;
    --rule: #6b6b6b;
    --panel-top: #c9c9c9;
    --panel-bottom: #ececec;
    --nav-top: #3a3a3a;
    --nav-bottom: #0e0e0e;
  }
  * { box-sizing: border-box; margin: 0; padding: 0; }
  html, body { width: 923px; height: 1200px; overflow: hidden; }
  body {
    position: relative;
    background: linear-gradient(var(--page) 0 143px, var(--ink) 143px);
    font-family: "Carlito", "Open Sans", sans-serif;
    color: var(--text);
  }
  .abs { position: absolute; }

  /* header */
  .brand { left: 36px; top: 42px; display: flex; align-items: center; gap: 10px; }
  .brand-dot { width: 60px; height: 60px; border-radius: 50%; background: #6d6d6d; }
  .brand-name { font-family: "Oswald", sans-serif; font-weight: 600; font-size: 40px; color: #555; letter-spacing: 0.5px; }
  .utility { right: 28px; top: 37px; font-family: "Open Sans", sans-serif; font-size: 9.5px; color: #222; word-spacing: 1px; }
  .search { left: 689px; top: 71px; width: 214px; height: 34px; border-radius: 17px; background: var(--ink); color: #bdbdbd; font-family: "Open Sans", sans-serif; font-size: 9.5px; line-height: 34px; padding-left: 16px; }

  /* navigation */
  .nav { left: 19px; top: 121px; width: 884px; height: 52px; display: flex; gap: 3px; background: #111; }
  .nav-item { height: 52px; display: flex; align-items: center; justify-content: center; font-family: "Oswald", sans-serif; font-size: 17px; letter-spacing: -0.2px; color: #fff; background: linear-gradient(var(--nav-top), var(--nav-bottom)); }
  .nav-item.is-active { background: linear-gradient(#f0c24c, var(--gold-deep)); color: #1a1a1a; }

  /* hero */
  .hero-photo { left: 20px; top: 182px; width: 611px; height: 303px; background: radial-gradient(circle at 45% 30%, #5f7f9e, #2c3440 60%, #1a1d22); }
  .hero-panel { left: 631px; top: 182px; width: 272px; height: 303px; background: linear-gradient(var(--panel-top), var(--panel-bottom)); }
  .hero-pointer { left: 608px; top: 214px; }
  .hero-line { position: absolute; left: 39px; font-family: "Oswald", sans-serif; font-size: 28px; letter-spacing: -0.3px; color: #262626; }
  .hero-rule { position: absolute; left: 18px; width: 236px; height: 1px; background: #333; }

  /* content */
  .content { left: 20px; top: 495px; width: 883px; height: 570px; background: var(--page); border-bottom: 5px solid #e4e4e4; }
  .heading { font-family: "Oswald", sans-serif; font-size: 21px; color: var(--gold); font-weight: 400; }
  .heading.dark { color: #1d1d1d; }
  .col-rule { left: 304px; top: 520px; width: 2px; height: 507px; background: var(--rule); }

  .events { left: 65px; top: 562px; list-style: none; font-family: "Open Sans", sans-serif; font-size: 13px; color: #555; letter-spacing: 1.8px; }
  .events li { height: 26px; }
  .events li::before { content: ">"; color: var(--gold); margin-right: 12px; letter-spacing: 0; }

  .news { left: 33px; width: 260px; font-size: 10.5px; line-height: 13.5px; text-align: justify; }
  .news-date { color: var(--gold-deep); font-size: 10.5px; margin-bottom: 8px; }
  .read-more { display: block; text-align: right; color: var(--gold-deep); font-size: 10.5px; margin-top: -3px; }

  .welcome-photo { left: 331px; top: 565px; width: 204px; height: 141px; border: 4px solid #fff; box-shadow: 0 1px 4px rgba(0,0,0,.45); background: linear-gradient(135deg, #1f5d86, #49a7cf 55%, #173247); }
  .copy { font-size: 12px; line-height: 16px; text-align: justify; }
  .copy p + p { margin-top: 15px; }

  .service { top: 905px; width: 171px; text-align: center; }
  .service-photo { height: 118px; border: 4px solid #fff; box-shadow: 0 1px 4px rgba(0,0,0,.45); }
  .service-name { font-family: "Oswald", sans-serif; font-size: 20px; color: #111; margin-top: 3px; }

  /* footer */
  .footer-nav { left: 0; top: 1091px; width: 923px; display: flex; justify-content: center; font-size: 10.5px; color: #fff; }
  .footer-nav span.sep { margin: 0 20px 0 22px; }
  .copyright { left: 0; top: 1124px; width: 923px; text-align: center; font-size: 10.5px; color: #fff; }
</style>
</head>
<body>
  <header>
    <div class="abs brand">
      <span class="brand-dot"></span>
      <span class="brand-name">Tarvex Summit</span>
    </div>
    <div class="abs utility">CLIENT LOGIN | SUPPORT | HELP</div>
    <div class="abs search">Search</div>
  </header>

  <nav class="abs nav">
    <a class="nav-item is-active" style="width:94px">Home</a>
    <a class="nav-item" style="width:109px">About Us</a>
    <a class="nav-item" style="width:127px">Innovation</a>
    <a class="nav-item" style="width:122px">Customers</a>
    <a class="nav-item" style="width:117px">Solutions</a>
    <a class="nav-item" style="width:92px">News</a>
    <a class="nav-item" style="width:99px">Career</a>
    <a class="nav-item" style="width:104px">Contact</a>
  </nav>

  <section class="hero">
    <div class="abs hero-photo" role="img" aria-label="Operator at a security monitoring desk with a wall of screens"></div>
    <div class="abs hero-panel">
      <div class="hero-line" style="top:30px">Sample text here</div>
      <div class="hero-rule" style="top:97px"></div>
      <div class="hero-line" style="top:122px">Sample text here</div>
      <div class="hero-rule" style="top:199px"></div>
      <div class="hero-line" style="top:230px">Sample text here</div>
    </div>
    <svg class="abs hero-pointer" width="24" height="36" viewBox="0 0 24 36"><polygon points="24,0 0,18 24,36" fill="#cbcbcb"/></svg>
  </section>

  <main class="abs content"></main>
  <div class="abs col-rule"></div>

  <h2 class="abs heading" style="left:33px; top:523px">Our Events</h2>
  <ul class="abs events">
    <li>Sample text of events</li><li>Sample text of events</li><li>Sample text of events</li>
    <li>Sample text of events</li><li>Sample text of events</li><li>Sample text of events</li>
    <li>Sample text of events</li><li>Sample text of events</li><li>Sample text of events</li>
    <li>Sample text of events</li>
  </ul>

  <h2 class="abs heading dark" style="left:33px; top:827px">Latest News</h2>
  <article class="abs news" style="top:873px">
    <div class="news-date">March 03.2012</div>
    <p>The council's formal responsibilities are to examine the expenditure, administration and policies of the security and intelligence teams as laid down in our charter; the Field Analysis Service.</p>
    <a class="read-more">READ MORE</a>
  </article>
  <article class="abs news" style="top:965px">
    <div class="news-date">March 03.2012</div>
    <p>The council's formal responsibilities are to examine the expenditure, administration and policies of the security and intelligence teams as laid down in our charter; the Field Analysis Service.</p>
    <a class="read-more">READ MORE</a>
  </article>

  <h1 class="abs heading" style="left:332px; top:523px">Welcome to Our Website</h1>
  <div class="abs welcome-photo" role="img" aria-label="Security officer in front of a wall of monitors"></div>
  <div class="abs copy" style="left:546px; top:563px; width:337px">
    <p>The Oversight and Readiness Council is a council of senior specialists appointed by the Board Chair to oversee the work of the intelligence practice of Tarvex Summit. It was established by the Founding Charter of 2011.</p>
    <p>The council's formal responsibilities are to examine the expenditure, administration and policies of the security and intelligence teams as laid down in our charter; the Field Analysis Service.</p>
  </div>
  <div class="abs copy" style="left:331px; top:728px; width:551px">
    <p>The members of the council are appointed under the Records Protection Policy 2011 and are given access to highly sensitive material in carrying out their duties. The council holds review sessions with program managers and senior officials (for example, the head of the Protective Operations Group). It also considers written input from the analysis and security teams and relevant client departments.</p>
    <p>The work of the council is normally conducted in private, though an open annual summary is issued. The council also produces reports on issues of particular concern, either on its own initiative or at the request of client program leaders.</p>
  </div>

  <h2 class="abs heading" style="left:332px; top:864px">Featured Services</h2>
  <div class="abs service" style="left:333px">
    <div class="service-photo" role="img" aria-label="Security officer at a monitoring wall" style="background:linear-gradient(135deg,#1f5d86,#49a7cf 55%,#173247)"></div>
    <div class="service-name">Service 1</div>
  </div>
  <div class="abs service" style="left:520px">
    <div class="service-photo" role="img" aria-label="Agent in a suit speaking into a radio" style="background:linear-gradient(90deg,#d9dcdc,#f2f2f2 40%,#3a3a3a 50%,#e6e8e8 60%,#cfd3d3)"></div>
    <div class="service-name">Service 2</div>
  </div>
  <div class="abs service" style="left:706px">
    <div class="service-photo" role="img" aria-label="Uniformed security guard standing at a gate" style="background:linear-gradient(90deg,#c8cacc,#e4e6e8 35%,#1e1f22 50%,#dfe1e3 65%,#b9bcbf)"></div>
    <div class="service-name">Service 3</div>
  </div>

  <footer>
    <div class="abs footer-nav">
      <span>Home</span><span class="sep">|</span><span>About Us</span><span class="sep">|</span><span>Innovation</span><span class="sep">|</span><span>Customers</span><span class="sep">|</span><span>Solutions</span><span class="sep">|</span><span>News</span><span class="sep">|</span><span>Career</span><span class="sep">|</span><span>Contact</span><span class="sep">|</span><span>Legal Notices</span>
    </div>
    <div class="abs copyright">Copyright 2012. All Rights Reserved.</div>
  </footer>
</body>
</html>
```